Popup Nightclub Grand Opening Flyer

We need to design a flyer for the grand opening of an upscale, exclusive nightclub called "Lantern". The design needs to be chic and exclusive. The background should be black and the text should primarily be white. We like minimalist designs.

Here is the text for the flyer
-
Velvetroll Atlanta Presents

Lantern (LOGO)

A Popup Nightclub Experience
For one night Only

Friday, October 18, 2013
Party begins at 9PM

INVITE ONLY

See invitation for location details
(Velvetroll Atlanta logo)

-
Examples we like

http://cdn4-x.pressfolio-example.com/sites/default/files/styles/image_content_width/hash/3b/fd/2468013579_4421_flyer.jpg?itok=K9rtQw2z

http://files.hubspace-example.net/files/8Hqq-Tr72WWE3kaRbTmcxP5QZK2F396J8nbRw4CKMHfdX2Y7qSEF-MqjxDoNrLY3QCyQJD7npjGaRq3k-Mhx6hqf3MDSWf8r3/2zenSaturdays.jpg

http://morvex-example.com/wp-content/uploads/siteskin/widgetkit/gallery/2zen/2zen-gen_qstay4-01.jpg

Hi All, one thing that we are seeing that we don't like is on over emphasis on the phrase "a popup nightclub experience" please don't make this the largest thing on the flyer

Target Market(s)

Target market is 25-35 year olds who are affluent (rich) and like luxury brands

Requirements
Must have
• Dark Background
Nice to have
• Velvetroll Logo on the bottom
Modern text that isn't curvy
Should not have
• Curved text

```html
<!DOCTYPE html>
<html lang="en">
<head>
<meta charset="utf-8">
<title>Lantern — A Popup Nightclub Experience</title>
<link href="https://fonts.googleapis.com/css2?family=Montserrat:wght@300;600;700&display=swap" rel="stylesheet">
<style>
  :root {
    --ink: #000000;
    --pattern-top: #1c1c1c;
    --pattern-mid: #111111;
    --grey: #8f8f8f;
    --grey-light: #b9b9b9;
    --white: #ffffff;
    --signal: #f5ef1f;
    --rule: #9a9a9a;
  }
  html, body {
    margin: 0;
    padding: 0;
    width: 827px;
    height: 1200px;
    overflow: hidden;
    background: var(--ink);
  }
  .flyer {
    position: relative;
    width: 827px;
    height: 1200px;
    background: var(--ink);
    font-family: "Montserrat", "Century Gothic", sans-serif;
    color: var(--white);
    overflow: hidden;
  }
  .damask-field {
    position: absolute;
    inset: 0 0 auto 0;
    height: 880px;
    background: radial-gradient(ellipse at 50% 35%, var(--pattern-top) 0%, var(--pattern-mid) 55%, var(--ink) 100%);
  }
  .line {
    position: absolute;
    left: 0;
    right: 0;
    margin: 0;
    text-align: center;
    text-transform: uppercase;
  }
  .presenter {
    top: 58px;
    font-weight: 700;
    font-size: 32px;
    line-height: 38px;
    color: var(--grey);
  }
  .mark-circle {
    position: absolute;
    left: 50%;
    top: 225px;
    transform: translateX(-50%);
  }
  .club-name {
    top: 598px;
    font-weight: 300;
    font-size: 50px;
    letter-spacing: 16px;
    padding-left: 16px;
    color: var(--grey-light);
  }
  .tagline {
    top: 737px;
    font-weight: 700;
    font-size: 35px;
    color: var(--white);
  }
  .tagline-rule {
    position: absolute;
    top: 790px;
    left: 188px;
    width: 452px;
    height: 2px;
    background: var(--rule);
  }
  .one-night {
    top: 800px;
    font-weight: 700;
    font-size: 54px;
    color: var(--signal);
    text-shadow: 0 0 18px rgba(245, 239, 31, 0.55);
  }
  .date-time {
    top: 872px;
    font-weight: 700;
    font-size: 30px;
    letter-spacing: 2px;
    color: var(--grey);
  }
  .invite {
    top: 1034px;
    font-weight: 700;
    font-size: 27px;
    color: var(--white);
  }
  .location-note {
    top: 1080px;
    font-weight: 600;
    font-size: 14px;
    color: var(--white);
  }
  .host-name {
    top: 1122px;
    font-weight: 600;
    font-size: 24px;
    letter-spacing: 3px;
    color: var(--grey-light);
  }
</style>
</head>
<body>
  <main class="flyer">
    <div class="damask-field" role="img" aria-label="Black damask ornament pattern background"></div>

    <p class="line presenter">Velvetroll Atlanta<br>Presents</p>

    <svg class="mark-circle" width="340" height="340" viewBox="0 0 340 340" aria-hidden="true">
      <circle cx="170" cy="170" r="150" fill="none" stroke="var(--grey-light)" stroke-width="6"/>
    </svg>

    <h1 class="line club-name">Lantern</h1>

    <p class="line tagline">A Popup Nightclub Experience</p>
    <div class="tagline-rule"></div>
    <p class="line one-night">For One Night Only</p>
    <p class="line date-time">Friday October 18 2013 @ 9:00PM</p>

    <p class="line invite">Invite Only</p>
    <p class="line location-note">See invitation for location details</p>
    <p class="line host-name">Velvetroll Atlanta</p>
  </main>
</body>
</html>
```